Interior Design & Furniture E commerce Website Design

I need a cutting edge website design, this is for Interior Design Services as well as eCommerce for furniture and home decor www.lorivexstudio.com
Here is a sample of the concept behind the site.
I am a furniture & Interior Designer, want to create a life style brand.
Will offer Interior Design Services : Commercial & Residential (this portion will be a catalog or portfolio type)
The eCommerce side will sell, Furniture, Lighting, Decor, Gifts, Textiles, will also be offering trade so that could be at bottom of site. I also like the concept of concierge as where all the info falls under: shipping, etc..

*Please make sure to make the eCommerce prominent.

Gathering more feedback

Hello Designers, I also would like to possibly update my logo, the current one I like but don't Love.

Target Market(s)

High end customers with disposable income, who also appreciate quality and unique furniture & design

Number of Pages Required

5+ page

Colors
0255a3
f37122

Requirements
Must have
• Room Planer: I will be using this tool http://qtstudio.velbarnix.com/room-planner.inc
• Live Chat
• Will be offering 3d renderings for spaces as well as Virtual Reality
• The image I loaded that looks like copper, I would like to have that as a color on the site with the texture: so the colors are Blue and copper. Would like the site to be user friendly and interactive
• http://qtstudio.velbarnix.com/ (this is the current site in development, so we will be offering Design your own, Trends, inspiration, etc...
• I have included a headshot to use for now about me. or about us.
• I also included several actual project installation (residential and commercial) as well as a variety of my furniture items
• I have Included an old Bio and some articles I would like to show case in a Press Area
• I would also like to include a section for Events (Giving back )I do a lot of charity events 1-2 a year and would like to showcase that as well
• *Please make the store (ecommerce prominent )

```html
<!DOCTYPE html>
<html lang="en">
<head>
<meta charset="utf-8">
<title>Lori Vex Studio</title>
<link href="https://fonts.googleapis.com/css2?family=Raleway:ital,wght@0,400;0,600;0,700;0,800;1,700;1,800&family=Open+Sans:wght@400;600;700&display=swap" rel="stylesheet">
<style>
:root{
  --navy:#1f3a68;
  --navy-deep:#1a3260;
  --copper:#b27a44;
  --copper-light:#c89360;
  --ink:#333a44;
  --muted:#7d838c;
  --grey-bg:#ededed;
  --line:#dcdcdc;
  --white:#ffffff;
}
*{margin:0;padding:0;box-sizing:border-box}
html,body{width:1200px;height:3804px;overflow:hidden}
body{position:relative;background:var(--white);font-family:"Open Sans",Arial,sans-serif;color:var(--ink)}
.abs{position:absolute}
.photo{position:absolute}

/* header */
.site-header{position:absolute;left:0;top:0;width:1200px;height:80px;background:rgba(255,255,255,.82);z-index:3}
.brand{position:absolute;left:104px;top:0;width:128px;height:148px;background:var(--navy);z-index:4;display:flex;flex-direction:column;align-items:center;justify-content:center;gap:10px}
.brand-mark{width:34px;height:34px;border:2px solid var(--copper-light)}
.brand-name{font-family:"Raleway",sans-serif;font-weight:700;font-size:13px;letter-spacing:2px;color:var(--copper-light);text-align:center;line-height:1.4}
.main-nav{position:absolute;left:248px;top:30px;display:flex;gap:22px;font-family:"Raleway",sans-serif;font-size:15px;font-weight:600;color:var(--ink);white-space:nowrap}
.main-nav .nav-services{color:var(--copper)}
.account-nav{position:absolute;right:40px;top:8px;display:flex;gap:22px;font-size:12px;color:var(--ink);align-items:center}
.account-nav span{display:flex;align-items:center;gap:6px}
.account-nav .signup{font-weight:700}

/* hero */
.hero{position:absolute;left:0;top:0;width:1200px;height:660px;background:linear-gradient(120deg,#cfcdca,#e7e4df 45%,#b7b3ad)}
.hero-collage{position:absolute;left:440px;top:184px;width:660px;height:420px;background:linear-gradient(135deg,#6d5644,#b49a7e 40%,#3e3a36 75%,#8b735c)}
.hero-band{position:absolute;left:160px;top:226px;width:940px;height:100px;background:rgba(30,30,30,.35);z-index:1}
.hero-title{position:absolute;left:176px;top:236px;font-family:"Raleway",sans-serif;font-style:italic;font-weight:800;font-size:38px;color:var(--white);letter-spacing:1px;z-index:2;white-space:nowrap}
.hero-sub{position:absolute;left:176px;top:288px;font-size:17px;color:var(--white);z-index:2;white-space:nowrap}
.hero-arrow{position:absolute;left:916px;top:532px;z-index:2}

/* trending */
.section-title{font-family:"Raleway",sans-serif;font-weight:700;color:var(--copper);font-size:38px}
.trending-title{position:absolute;left:80px;top:722px}
.slider-btn{position:absolute;top:724px;width:40px;height:40px;border-radius:50%;background:var(--navy);display:flex;align-items:center;justify-content:center}
.product-card{position:absolute;top:812px;width:248px;height:388px;border:1px solid var(--line);background:var(--white)}
.product-card .photo{left:24px;top:20px;width:200px;height:190px}
.product-name{position:absolute;left:24px;top:236px;font-family:"Raleway",sans-serif;font-weight:700;font-size:14px;color:var(--ink)}
.product-desc{position:absolute;left:24px;top:262px;width:190px;font-size:13px;line-height:18px;color:var(--muted)}
.product-price{position:absolute;left:24px;top:312px;font-family:"Raleway",sans-serif;font-weight:700;font-size:26px;color:var(--ink)}
.product-card.is-active{background:var(--navy);border-color:var(--navy)}
.product-card.is-active .product-name,.product-card.is-active .product-desc,.product-card.is-active .product-price{color:var(--white)}
.cart-tag{position:absolute;left:0;top:0;width:0;height:0;border-top:40px solid var(--navy);border-right:40px solid transparent}

/* about */
.about{position:absolute;left:0;top:1272px;width:1200px;height:568px;background:var(--grey-bg)}
.about .photo{left:0;top:0;width:520px;height:568px;background:linear-gradient(110deg,#d9d9d9,#8e8e8e 55%,#3d3d3d)}
.about-title{position:absolute;left:560px;top:68px;font-size:38px}
.about-text{position:absolute;left:560px;top:132px;width:560px;font-size:13px;line-height:22px;color:var(--muted)}
.about-text p+p{margin-top:8px}
.btn{position:absolute;background:var(--navy);color:var(--white);font-family:"Raleway",sans-serif;font-weight:700;font-size:14px;letter-spacing:1px;display:flex;align-items:center;justify-content:center}
.about .btn{left:560px;top:456px;width:168px;height:48px}

/* articles */
.articles-title{position:absolute;left:0;top:1900px;width:1200px;text-align:center}
.article .photo{top:1980px;width:260px;height:332px;border:1px solid var(--line)}
.article-caption{position:absolute;top:2334px;width:300px;text-align:center;font-family:"Raleway",sans-serif;font-weight:700;font-size:17px;line-height:24px;color:var(--ink)}

/* testimonial */
.testimonial{position:absolute;left:0;top:2448px;width:1200px;height:572px;background:linear-gradient(180deg,#e4e3e1,#d2d0cc 70%,#b7a58e)}
.testimonial-title{position:absolute;left:0;top:60px;width:1200px;text-align:center;font-size:38px}
.client-photo{position:absolute;left:528px;top:120px;width:144px;height:144px;border-radius:50%;border:5px solid var(--white);background:linear-gradient(160deg,#a89685,#5e5248)}
.quote-text{position:absolute;left:300px;top:292px;width:600px;text-align:center;font-size:14px;line-height:22px;font-style:italic;color:var(--ink)}
.client-name{position:absolute;left:0;top:390px;width:1200px;text-align:center;font-family:"Raleway",sans-serif;font-weight:700;font-size:14px;color:var(--navy);letter-spacing:1px}
.client-name::before,.client-name::after{content:"";display:inline-block;width:40px;height:1px;background:var(--navy);vertical-align:middle;margin:0 10px}
.dots{position:absolute;left:572px;top:424px;display:flex;gap:10px}
.dots i{width:10px;height:10px;border-radius:50%;background:#9aa0a8}
.dots i:first-child{background:var(--navy)}
.speaker{position:absolute;top:240px;width:56px;height:260px;background:#2a2a2a}
.quote-mark{position:absolute;font-family:Georgia,serif;font-size:140px;color:rgba(255,255,255,.7);line-height:1}

/* news boxes */
.news-box{position:absolute;top:3060px;width:332px;height:300px}
.news-head{height:48px;background:var(--navy);color:var(--white);font-family:"Raleway",sans-serif;font-weight:700;font-size:16px;letter-spacing:1px;display:flex;align-items:center;justify-content:center}
.news-box .photo{position:relative;height:252px}

/* footer */
.site-footer{position:absolute;left:0;top:3420px;width:1200px;height:384px;background:var(--navy-deep)}
.footer-brand{position:absolute;left:0;top:60px;width:1200px;text-align:center;display:flex;flex-direction:column;align-items:center;gap:10px}
.social{position:absolute;left:536px;top:214px;display:flex;gap:16px}
.social i{width:36px;height:36px;border-radius:50%;background:var(--copper)}
.footer-links{position:absolute;left:0;top:280px;width:1200px;text-align:center;font-size:13px;color:var(--white)}
.footer-links span{margin:0 10px}
.footer-links em{font-style:normal;opacity:.6}
.copyright{position:absolute;left:0;top:318px;width:1200px;text-align:center;font-size:11px;color:rgba(255,255,255,.7)}
</style>
</head>
<body>

<section class="hero">
  <div class="photo" role="img" aria-label="Softly blurred living room interior with a plant and window light" style="left:0;top:0;width:1200px;height:660px;background:radial-gradient(ellipse at 20% 70%,#bdb9b2,transparent 60%),radial-gradient(ellipse at 85% 40%,#d5d2cc,transparent 60%)"></div>
  <div class="hero-collage" role="img" aria-label="Collage of residential and commercial interior projects and furniture pieces"></div>
  <div class="hero-band"></div>
  <h1 class="hero-title">LORI VEX STUDIO</h1>
  <p class="hero-sub">I am a furniture &amp; Interior Designer, want to create a life style brand.</p>
  <svg class="hero-arrow" width="40" height="32" viewBox="0 0 40 32"><path d="M2 16h32M22 4l12 12-12 12" stroke="#1f3a68" stroke-width="5" fill="none"/></svg>
</section>

<header class="site-header">
  <nav class="main-nav">
    <span>Living Room</span><span>Dining Room</span><span>Bedroom</span><span>Home Office</span><span>Entertainment</span><span>Wellness</span><span>Accessories</span><span class="nav-services">DESIGN SERVICES</span>
  </nav>
  <div class="account-nav">
    <span><svg width="12" height="12" viewBox="0 0 12 12"><path d="M2 1l3 1-1 3 3 3 3-1 1 3-2 2C5 11 1 7 0 3z" fill="#333a44"/></svg>Contact Us</span>
    <span><svg width="12" height="12" viewBox="0 0 12 12"><circle cx="6" cy="4" r="3" fill="#333a44"/><path d="M0 12c0-4 12-4 12 0z" fill="#333a44"/></svg>My Account</span>
    <span class="signup"><svg width="12" height="12" viewBox="0 0 12 12"><rect x="2" y="5" width="8" height="7" fill="#333a44"/><path d="M4 5V3a2 2 0 0 1 4 0v2" stroke="#333a44" fill="none" stroke-width="1.5"/></svg>SIGN UP</span>
  </div>
</header>
<div class="brand">
  <div class="brand-mark"></div>
  <div class="brand-name">LORI VEX<br>STUDIO</div>
</div>

<h2 class="section-title trending-title">What's Trending Now...</h2>
<div class="slider-btn" style="left:1032px"><svg width="12" height="14" viewBox="0 0 12 14"><path d="M9 1L3 7l6 6" stroke="#fff" stroke-width="2.5" fill="none"/></svg></div>
<div class="slider-btn" style="left:1084px"><svg width="12" height="14" viewBox="0 0 12 14"><path d="M3 1l6 6-6 6" stroke="#fff" stroke-width="2.5" fill="none"/></svg></div>

<article class="product-card" style="left:80px">
  <div class="photo" role="img" aria-label="Upholstered lounge armchair" style="background:radial-gradient(circle,#d9d3cb,#fff 72%)"></div>
  <div class="product-name">PRODUCT NAME</div>
  <div class="product-desc">Lorem ipsum simple text is printing industry</div>
  <div class="product-price">$55.99</div>
</article>
<article class="product-card is-active" style="left:344px">
  <div class="photo" role="img" aria-label="Carved chair with red seat" style="left:0;top:0;width:248px;height:224px;background:radial-gradient(circle,#8c3b2e,#e9e6e1 70%)"></div>
  <div class="cart-tag" style="border-top-color:#16305a"></div>
  <div class="product-name">PRODUCT NAME</div>
  <div class="product-desc">Lorem ipsum simple text is printing industry</div>
  <div class="product-price">$55.99</div>
  <svg class="abs" style="left:196px;top:330px" width="32" height="20" viewBox="0 0 32 20"><path d="M0 10h26M18 3l8 7-8 7" stroke="#fff" stroke-width="3" fill="none"/></svg>
</article>
<article class="product-card" style="left:608px">
  <div class="photo" role="img" aria-label="Lacquered side table with metal legs" style="background:radial-gradient(circle,#5a4a3a,#fff 72%)"></div>
  <div class="product-name">PRODUCT NAME</div>
  <div class="product-desc">Lorem ipsum simple text is printing industry</div>
  <div class="product-price">$55.99</div>
</article>
<article class="product-card" style="left:872px">
  <div class="photo" role="img" aria-label="Ornate gold decorative cabinet" style="background:radial-gradient(circle,#b48a4a,#fff 72%)"></div>
  <div class="product-name">PRODUCT NAME</div>
  <div class="product-desc">Lorem ipsum simple text is printing industry</div>
  <div class="product-price">$55.99</div>
</article>

<section class="about">
  <div class="photo" role="img" aria-label="Black and white portrait of the designer"></div>
  <h2 class="section-title about-title">About Lori Vex</h2>
  <div class="about-text">
    <p>As a child, Lori Vex spent hours in her father's workshop learning how fine furniture is shaped, joined and finished by hand. That early love of craft grew into a design practice built on quality, patience and a respect for materials. After years creating rooms for private homes, boutique hotels and restaurants, she founded her own studio to bring a complete lifestyle vision to clients. Today the studio designs residential and commercial interiors, produces its own furniture collections and works closely with artisans across the world.</p>
    <p>Lori believes every space should tell a personal story, and she guides each project from the first sketch to the final detail with care.</p>
  </div>
  <div class="btn">LEARN MORE</div>
</section>

<h2 class="section-title articles-title">Recent Articlles</h2>
<div class="article">
  <div class="photo" role="img" aria-label="Black and white magazine cover featuring the studio" style="left:160px;background:linear-gradient(180deg,#f2f2f2 18%,#9a9a9a 40%,#3c3c3c 80%,#cfcfcf)"></div>
  <div class="article-caption" style="left:140px">Lorem Ipsum simple text<br>is printing industry</div>
</div>
<div class="article">
  <div class="photo" role="img" aria-label="Colourful magazine cover featuring the studio" style="left:470px;background:linear-gradient(180deg,#f5f5f5 18%,#5a3d8f 35%,#b23a7a 65%,#2d3f8f)"></div>
  <div class="article-caption" style="left:450px">Lorem Ipsum simple text<br>is printing industry</div>
</div>
<div class="article">
  <div class="photo" role="img" aria-label="Open magazine page with interior project article" style="left:780px;background:linear-gradient(90deg,#6b4a33 0,#a47a55 45%,#f4f1ec 46%,#ece8e2)"></div>
  <div class="article-caption" style="left:760px">Lorem Ipsum simple text<br>is printing industry</div>
</div>

<section class="testimonial" role="img" aria-label="Soft living room backdrop with speakers and plants">
  <div class="speaker" style="left:64px"></div>
  <div class="speaker" style="left:1080px"></div>
  <div class="quote-mark" style="left:230px;top:200px">&#8220;</div>
  <div class="quote-mark" style="left:880px;top:330px">&#8221;</div>
  <h2 class="section-title testimonial-title">What Our Client Say About Us</h2>
  <div class="client-photo"></div>
  <p class="quote-text">" Lorem Ipsum is simply dummy text of the printing and typesetting industry. Lorem Ipsum has been the industry's standard dummy text ever since the 1500s, when an unknown printer took a galley of type and scrambled it to make a type specimen book. it has sur"</p>
  <div class="client-name">CLIENT NAME</div>
  <div class="dots"><i></i><i></i><i></i></div>
</section>

<div class="news-box" style="left:80px">
  <div class="news-head">LATEST NEWS</div>
  <div class="photo" role="img" aria-label="Designer at a furniture showroom event" style="background:linear-gradient(135deg,#5d4a36,#a08562 50%,#3f3427)"></div>
</div>
<div class="news-box" style="left:440px">
  <div class="news-head">LATEST EVENTS</div>
  <div class="photo" role="img" aria-label="Restaurant interior with red lighting" style="background:linear-gradient(135deg,#7a2a22,#c2623d 50%,#4a1e1a)"></div>
</div>
<div class="news-box" style="left:788px">
  <div class="news-head">CHARITY EVENTS</div>
  <div class="photo" role="img" aria-label="Collage of charity event interiors" style="background:linear-gradient(135deg,#9a8b78,#d8cfc2 50%,#5e5448)"></div>
</div>

<footer class="site-footer">
  <div class="footer-brand">
    <div class="brand-mark" style="width:48px;height:48px"></div>
    <div class="brand-name" style="font-size:16px">LORI VEX<br>STUDIO</div>
  </div>
  <div class="social"><i></i><i></i><i></i><i></i></div>
  <div class="footer-links"><span>Home</span><em>|</em><span>About Us</span><em>|</em><span>Products</span><em>|</em><span>Blog</span><em>|</em><span>Event</span><em>|</em><span>News</span><em>|</em><span>Articles</span><em>|</em><span>Contact Us</span></div>
  <div class="copyright">LORI VEX STUDIO - 2015 All Right Reserved</div>
</footer>

</body>
</html>
```